Pet label template for Vantoreli mexican based company

Hello, Vantoreli is a mexican based company dedicated to manufacture and sell its propietary brands for human health care. We are now introducing a new "Pet" category to our Brand. It´s name is Vantoreli Pets (logo attached).
We are lookoig for the design template for our package labels that will most probably be in plastic bags like the example attaches (Pet meadows of brookfield). It is important to point out that the labels are going to be pasted on the bags and not directly printed on the bags itself like the examples attached.

I am attaching some examples but please feel free to innovate your own desing. I am also attaching the logo that must be in every label.

Target Market(s)

Pet owners basically dogs and cats.

Industry/Entity Type

Health Care

Font styles to use
Other font styles liked:
• something easy to read

Requirements
Must have
• We like both simple elegant designs and bright colorful ones son feel free to innovate.
Nice to have
• Illustration of both cat or dog for their product label.

```html
<!DOCTYPE html>
<html lang="en">
<head>
<meta charset="utf-8">
<title>Vantoreli Pets – Immunity Label</title>
<link rel="stylesheet" href="https://fonts.googleapis.com/css2?family=Fredoka:wght@600&family=Roboto+Condensed:wght@700&display=swap">
<style>
  :root {
    --bg: #e4e2df;
    --green-light: #68d63a;
    --green-mid: #4fb52e;
    --green-deep: #3b9426;
    --green-dark: #1f6a33;
    --lime: #d2f53c;
    --white: #ffffff;
    --ink: #111111;
    --silhouette: #1a1a1a;
    --label-green-text: #2f8a1f;
  }
  * { margin: 0; padding: 0; box-sizing: border-box; }
  html, body {
    width: 1200px; height: 1115px; overflow: hidden;
    background: var(--bg);
    font-family: "Roboto Condensed", "Arial Narrow", sans-serif;
    font-weight: 700;
  }
  .label {
    position: absolute; left: 190px; top: 57px;
    width: 820px; height: 1000px;
    overflow: hidden;
    background: var(--white);
  }
  .label-art { position: absolute; inset: 0; }
  .brand {
    position: absolute; top: 70px; left: 0; width: 100%;
    display: flex; justify-content: center; align-items: center; gap: 14px;
  }
  .brand-dot {
    width: 34px; height: 34px; border-radius: 50%;
    background: var(--white);
  }
  .brand-name {
    color: var(--white); font-weight: 700; font-size: 46px;
    letter-spacing: 2px; text-transform: uppercase; white-space: nowrap;
  }
  .product-title {
    position: absolute; top: 160px; left: 0; width: 100%;
    text-align: center;
    font-family: "Fredoka", "Arial Rounded MT Bold", sans-serif;
    font-weight: 600; font-size: 132px; line-height: 1;
    color: var(--white);
    -webkit-text-stroke: 3px var(--green-dark);
    paint-order: stroke fill;
    text-shadow: 0 4px 0 var(--lime);
    white-space: nowrap;
  }
  .product-tagline {
    position: absolute; top: 291px; left: 137px; width: 546px; height: 20px;
    background: var(--green-dark);
    color: var(--white); font-size: 14px; line-height: 20px;
    text-align: center; letter-spacing: 0.5px; white-space: nowrap;
  }
  .ingredients {
    position: absolute; top: 322px; left: 0; width: 100%;
    text-align: center; font-size: 27px; color: var(--ink);
    letter-spacing: 0.5px; white-space: nowrap;
  }
  .benefits {
    position: absolute; top: 370px; left: 215px; list-style: none;
  }
  .benefit {
    display: flex; align-items: center; height: 50px;
  }
  .benefit-icon { width: 42px; height: 38px; margin-right: 40px; flex: none; }
  .benefit-text {
    color: var(--white); font-size: 23px; line-height: 28px; width: 300px;
    white-space: nowrap;
    border-bottom: 2px dotted var(--white); padding-bottom: 3px;
  }
  .benefit-text::before { content: "✓ "; font-size: 17px; }
  .pets-illustration {
    position: absolute; left: 300px; top: 610px;
    width: 350px; height: 280px; border-radius: 40px 40px 12px 12px;
    background: linear-gradient(180deg, #2c2c2c, var(--silhouette));
  }
  .grain-free {
    position: absolute; top: 910px; left: 270px; width: 220px;
    text-align: center; color: var(--label-green-text);
    font-size: 30px; line-height: 1; white-space: nowrap;
  }
  .grain-free-dot {
    display: inline-block; width: 18px; height: 18px; border-radius: 50%;
    background: var(--green-mid); margin-right: 6px; vertical-align: 2px;
  }
  .net-weight {
    position: absolute; top: 948px; left: 262px; width: 236px;
    text-align: center; color: var(--label-green-text); font-size: 17px;
    white-space: nowrap;
  }
</style>
</head>
<body>
  <main class="label">
    <svg class="label-art" viewBox="0 0 820 1000" width="820" height="1000" aria-hidden="true">
      <defs>
        <linearGradient id="greenField" x1="0" y1="0" x2="0" y2="1">
          <stop offset="0" stop-color="#6ad93c"/>
          <stop offset="0.55" stop-color="#52b92f"/>
          <stop offset="1" stop-color="#3b9426"/>
        </linearGradient>
      </defs>
      <rect class="green-field" width="820" height="1000" fill="url(#greenField)"/>
      <path class="swoosh-lime" d="M0,850 C210,680 470,520 820,480 L820,510 C500,545 230,690 0,880 Z" fill="var(--lime)"/>
      <path class="swoosh-green" d="M0,868 C220,700 480,540 820,500 L820,512 C500,550 235,700 0,890 Z" fill="var(--green-mid)"/>
      <path class="white-field" d="M0,890 C235,705 500,552 820,514 L820,1000 L0,1000 Z" fill="var(--white)"/>
    </svg>

    <div class="brand">
      <span class="brand-dot"></span>
      <span class="brand-name">Vantoreli Pets</span>
    </div>

    <h1 class="product-title">Immunity</h1>
    <div class="product-tagline">IMMUNE SUPPORT FOR PETS</div>
    <p class="ingredients">PROBIOTICS • VITAMINS • ANTIOXIDANTS</p>

    <ul class="benefits">
      <li class="benefit">
        <svg class="benefit-icon" viewBox="0 0 42 38" aria-hidden="true">
          <path d="M21 3 L36 8 V18 C36 27 29 33 21 36 C13 33 6 27 6 18 V8 Z" fill="none" stroke="#fff" stroke-width="3"/>
          <path d="M14 19 L19 24 L28 14" fill="none" stroke="#fff" stroke-width="3"/>
        </svg>
        <span class="benefit-text">SUPPORT IMMUNE SYSTEM</span>
      </li>
      <li class="benefit">
        <svg class="benefit-icon" viewBox="0 0 42 38" aria-hidden="true">
          <path d="M21 35 C8 26 3 19 3 12 C3 6 8 2 13 2 C17 2 20 5 21 7 C22 5 25 2 29 2 C34 2 39 6 39 12 C39 19 34 26 21 35 Z" fill="#fff"/>
          <path d="M6 18 H15 L18 12 L23 24 L26 18 H36" fill="none" stroke="var(--green-mid)" stroke-width="2.5"/>
        </svg>
        <span class="benefit-text">CARDIOVASCULAR SYSTEM</span>
      </li>
      <li class="benefit">
        <svg class="benefit-icon" viewBox="0 0 42 38" aria-hidden="true">
          <circle cx="21" cy="19" r="14" fill="#fff"/>
        </svg>
        <span class="benefit-text">LIVER FUNCTION</span>
      </li>
    </ul>

    <div class="pets-illustration" role="img" aria-label="Black silhouettes of a cat and a large dog sitting side by side"></div>

    <p class="grain-free"><span class="grain-free-dot"></span>GRAIN FREE</p>
    <p class="net-weight">NET WT 2.12 OZ. (90G)</p>
  </main>
</body>
</html>
```